New Electrical Business Card Design

I would like a new design for my business cards.
i would like the same logo and font but new design
Please see attached files for front and back design.
large image can be used for graphics.
I would like the instagram link incorporated to back of card.
website site address needs to be changed to www.kestrelhillelectrical.au
everything else stays as is

```html
<!DOCTYPE html>
<html lang="en">
<head>
<meta charset="utf-8">
<title>Kestrel Hill – Business Card</title>
<link rel="stylesheet" href="https://fonts.googleapis.com/css2?family=Archivo:wght@400;500;700;900&display=swap">
<style>
  :root {
    --page: #d9d9d9;
    --card: #232323;
    --green: #0f7a3e;
    --green-text: #149148;
    --white: #ffffff;
    --grey: #9a9a9a;
    --divider: #6b6b6b;
  }
  * { box-sizing: border-box; margin: 0; padding: 0; }
  html, body { width: 1200px; height: 800px; overflow: hidden; }
  body {
    background: var(--page);
    font-family: "Archivo", Arial, sans-serif;
    display: flex;
    flex-direction: column;
    align-items: center;
    justify-content: center;
    gap: 40px;
  }
  .card {
    width: 560px;
    height: 340px;
    background: var(--card);
    border-radius: 22px;
    position: relative;
    overflow: hidden;
    color: var(--white);
  }
  .cards { display: flex; gap: 40px; }

  .brand {
    display: flex;
    align-items: center;
    gap: 12px;
    font-weight: 900;
    font-size: 48px;
    letter-spacing: -0.5px;
    line-height: 1;
    color: var(--white);
    text-transform: uppercase;
  }
  .brand-dot {
    width: 30px; height: 30px;
    border-radius: 50%;
    background: var(--green);
    flex: none;
  }

  /* Front */
  .card-front .brand { position: absolute; top: 62px; left: 0; right: 0; justify-content: center; }
  .details {
    position: absolute;
    top: 150px; left: 40px; right: 30px;
    display: flex;
    align-items: center;
    justify-content: center;
    gap: 22px;
  }
  .holder { text-align: right; }
  .holder-name { color: var(--green-text); font-weight: 700; font-size: 20px; letter-spacing: 0.3px; text-transform: uppercase; }
  .holder-line { font-size: 14px; margin-top: 4px; color: var(--white); }
  .holder-line .label { color: var(--green-text); }
  .divider { width: 1px; height: 74px; background: var(--divider); }
  .contacts { list-style: none; font-size: 14px; }
  .contacts li { display: flex; align-items: center; gap: 8px; margin: 4px 0; }
  .contacts svg { width: 13px; height: 13px; flex: none; }
  .service-band {
    position: absolute; left: 0; right: 0; bottom: 32px;
    height: 40px;
    background: var(--green);
    display: flex; align-items: center; justify-content: center;
    font-size: 19px; font-weight: 500; letter-spacing: 0.3px;
  }

  /* Back */
  .card-back .brand { position: absolute; top: 130px; left: 0; right: 0; justify-content: center; }
  .social {
    position: absolute; top: 230px; left: 0; right: 0;
    display: flex; justify-content: center; align-items: center; gap: 10px;
    font-size: 20px;
  }
  .social-dot { width: 20px; height: 20px; border-radius: 50%; background: var(--green); }
</style>
</head>
<body>
  <div class="cards">
    <section class="card card-front">
      <div class="brand"><span class="brand-dot"></span>Kestrel Hill</div>
      <div class="details">
        <div class="holder">
          <p class="holder-name">Daniel Harwood</p>
          <p class="holder-line"><span class="label">ABN</span> - 12 345 678 901</p>
          <p class="holder-line"><span class="label">Lic number</span> - 318844C</p>
        </div>
        <div class="divider"></div>
        <ul class="contacts">
          <li><svg viewBox="0 0 16 16"><path fill="#149148" d="M3.6 1.5l2.3 2.6-1.3 1.8c.9 2 2.5 3.6 4.5 4.5l1.8-1.3 2.6 2.3-1.2 2.1C7 13.3 2.7 9 2.5 3.7z"/></svg>0400 555 218</li>
          <li><svg viewBox="0 0 16 16"><rect x="1" y="3" width="14" height="10" fill="#149148"/><path d="M1 3l7 6 7-6" stroke="#232323" stroke-width="1.4" fill="none"/></svg>info@kestrelhillelectrical.au</li>
          <li><svg viewBox="0 0 16 16"><circle cx="8" cy="8" r="7" fill="#149148"/><path d="M1 8h14M8 1c-3 4-3 10 0 14M8 1c3 4 3 10 0 14" stroke="#232323" stroke-width="1" fill="none"/></svg>www.kestrelhillelectrical.au</li>
        </ul>
      </div>
      <div class="service-band">Residential • Commercial • Industrial • 24hr service</div>
    </section>

    <section class="card card-back">
      <div class="brand"><span class="brand-dot"></span>Kestrel Hill</div>
      <div class="social"><span class="social-dot"></span>kestrel.hill.electrical</div>
    </section>
  </div>
</body>
</html>
```